Business Card Design Project

We are not a new company, but renamed to "Vantorin Kitchens" last year. We specialize in modern high-end cabinetry imports. We would like to communicate a sense of quality and cutting edge technology. Ideally the design would incorporate our logo colors, silver, red and preferably a black, matte background. Though we are open to suggestions.
Logo is attached.
Edit: I have attached rough drafts of the previous cards, this way you will have all necessary content that needs to go on the cards.
Updates
Project Deadline Extended
Reason: We have received a lot of great designs, but due to the sheer number we couldn't respond to all. We will extend the deadline for another 7 days to finalize and provide feedback to designers.
Thank you for your hard work!
Industry/Entity Type
Business
Look and feel
Each slider illustrates characteristics of the customer's brand and the style your logo design should communicate.

```html
<!DOCTYPE html>
<html lang="en">
<head>
<meta charset="utf-8">
<title>Vantorin Kitchens – Business Cards</title>
<link rel="stylesheet" href="https://fonts.googleapis.com/css2?family=Michroma&display=swap">
<style>
  :root {
    --page: #e8e4df;
    --card-dark: #111214;
    --card-mid: #26282b;
    --silver-light: #e6e7e8;
    --silver: #b9bbbe;
    --silver-dark: #7d7f83;
    --red: #ed1c24;
    --text-light: #f2f2f2;
    --band-text: #ffffff;
  }
  * { margin: 0; padding: 0; box-sizing: border-box; }
  html, body {
    width: 1200px; height: 788px; overflow: hidden;
    background: var(--page);
    font-family: "Michroma", sans-serif;
  }
  .sheet { position: relative; width: 1200px; height: 788px; }

  .card {
    position: absolute; width: 525px; height: 300px;
    border-radius: 20px; overflow: hidden;
    background: radial-gradient(ellipse at 50% 35%, var(--card-mid) 0%, var(--card-dark) 75%);
  }
  .card--matte { background: #050505; }
  .card--front { left: 50px; top: 62px; }
  .card--front-alt { left: 628px; top: 62px; }
  .card--back { left: 57px; top: 447px; }
  .card--back-alt { left: 624px; top: 446px; }

  .wordmark {
    position: absolute; left: 0; right: 0;
    display: flex; align-items: center; justify-content: center; gap: 12px;
    color: var(--silver); letter-spacing: 1px; text-transform: uppercase;
  }
  .wordmark__square { width: 14px; height: 14px; background: var(--red); }
  .card--front .wordmark, .card--front-alt .wordmark { top: 96px; font-size: 20px; }
  .card--back .wordmark, .card--back-alt .wordmark { top: 160px; font-size: 22px; }

  .name-band {
    position: absolute; left: 0; top: 156px; width: 452px; height: 35px;
    background: linear-gradient(90deg, var(--silver-dark) 0%, var(--silver-light) 45%, var(--silver) 75%, var(--silver-dark) 100%);
    display: flex; align-items: center; justify-content: center;
    color: var(--band-text); font-size: 15px; letter-spacing: 3px;
    text-shadow: 0 1px 1px rgba(0,0,0,0.35);
  }
  .name-band__role { font-size: 9px; letter-spacing: 1px; margin-left: 6px; }
  .red-tab {
    position: absolute; left: 458px; top: 156px; width: 67px; height: 35px;
    background: var(--red);
  }

  .contacts {
    position: absolute; left: 44px; top: 213px; list-style: none;
    color: var(--text-light); font-size: 10.5px; letter-spacing: 1.5px;
  }
  .contacts li { display: flex; align-items: center; height: 19.7px; }
  .contacts svg { width: 11px; height: 11px; margin-right: 7px; fill: var(--silver); }
  .contacts .email { font-size: 9px; letter-spacing: 1px; }

  .address {
    position: absolute; left: 353px; top: 236px;
    color: var(--text-light); font-size: 10px; letter-spacing: 1.5px; line-height: 18px;
  }

  .perforation {
    position: absolute; width: 290px; height: 110px;
    background: radial-gradient(ellipse at center, #5a5c60 0%, #2a2b2e 45%, rgba(5,5,5,0) 75%);
  }
  .perforation--top { left: 0; top: -10px; }
  .perforation--bottom { right: 0; bottom: -10px; }
</style>
</head>
<body>
<main class="sheet">

  <section class="card card--front" aria-label="Front, Marek Dolan">
    <div class="wordmark"><span class="wordmark__square"></span>Vantorin Kitchens</div>
    <div class="name-band">MAREK DOLAN,<span class="name-band__role">PRESIDENT</span></div>
    <div class="red-tab"></div>
    <ul class="contacts">
      <li><svg viewBox="0 0 12 12"><path d="M3 1l2 2-1 2c1 1.5 2 2.5 3 3l2-1 2 2-2 2C4 11 1 8 1 3z"/></svg>555.201.0147</li>
      <li><svg viewBox="0 0 12 12"><rect x="1" y="4" width="10" height="6" rx="1"/><rect x="3" y="1" width="6" height="3"/></svg>555.201.0148</li>
      <li><svg viewBox="0 0 12 12"><rect x="3.5" y="0.5" width="5" height="11" rx="1"/></svg>555.201.0393</li>
      <li class="email"><svg viewBox="0 0 12 12"><path d="M1 3h10v7H1z M1 3l5 4 5-4" stroke="#111" stroke-width="0.8"/></svg>marek@vantorinkitchens.ca</li>
    </ul>
    <div class="address">4812 - 76 St.<br>Ridgemont<br>AB T0X 4K2</div>
  </section>

  <section class="card card--front-alt card--matte" aria-label="Front, Tomas Dolan">
    <div class="wordmark"><span class="wordmark__square"></span>Vantorin Kitchens</div>
    <div class="name-band">TOMAS DOLAN,<span class="name-band__role">DIRECTOR</span></div>
    <div class="red-tab"></div>
    <ul class="contacts">
      <li><svg viewBox="0 0 12 12"><path d="M3 1l2 2-1 2c1 1.5 2 2.5 3 3l2-1 2 2-2 2C4 11 1 8 1 3z"/></svg>555.201.0147</li>
      <li><svg viewBox="0 0 12 12"><rect x="1" y="4" width="10" height="6" rx="1"/><rect x="3" y="1" width="6" height="3"/></svg>555.201.0148</li>
      <li><svg viewBox="0 0 12 12"><rect x="3.5" y="0.5" width="5" height="11" rx="1"/></svg>555.201.0462</li>
      <li class="email"><svg viewBox="0 0 12 12"><path d="M1 3h10v7H1z M1 3l5 4 5-4" stroke="#111" stroke-width="0.8"/></svg>tomas@vantorinkitchens.ca</li>
    </ul>
    <div class="address">4812 - 76 St.<br>Ridgemont<br>AB T0X 4K2</div>
  </section>

  <section class="card card--back" aria-label="Back">
    <div class="wordmark"><span class="wordmark__square"></span>Vantorin Kitchens</div>
  </section>

  <section class="card card--back-alt card--matte" aria-label="Back, alternate">
    <div class="perforation perforation--top" role="img" aria-label="Perforated metal texture"></div>
    <div class="perforation perforation--bottom" role="img" aria-label="Perforated metal texture"></div>
    <div class="wordmark"><span class="wordmark__square"></span>Vantorin Kitchens</div>
  </section>

</main>
</body>
</html>
```